Real Estate 2015 sold listings postcard

Real estate. I want one side to list 2015 sales. Mailing side with additional information. I am including a "concept" but it needs to be professionalized... Feel free to change color, fonts, layout, add watermark, whatever you think will work. Text on backside may be tweaked. I do want postcards addressed. How do i send mailing list or does Kestro mail do that part?

NOTE: Postcard should be 8.5 x 5.5 inches.
Updates

postcard should be 8.5" x 5.5" size

Target Market(s)

Home owners who may want to sell

Industry/Entity Type

Real Estate Agent

Requirements
Must have
• The sold information and contact oinformation I have provided
Nice to have
• Watermark with my initials

```html
<!DOCTYPE html>
<html lang="en">
<head>
<meta charset="utf-8">
<title>2015 Sales Postcard</title>
<link href="https://fonts.googleapis.com/css2?family=Lato:wght@300;400;700;900&display=swap" rel="stylesheet">
<style>
:root{
  --red:#d8232f;
  --red-dark:#a8141f;
  --gold:#c9a12a;
  --gray:#bdbdbd;
  --ink:#2b2b2b;
  --muted:#6b6b6b;
  --paper:#ffffff;
  --bg:#e8e8e8;
}
*{box-sizing:border-box;margin:0;padding:0}
html,body{width:1200px;height:800px;overflow:hidden;background:var(--bg);font-family:'Lato',sans-serif}
.frame{position:absolute;top:211px;width:583px;height:377px;box-shadow:0 4px 14px rgba(0,0,0,.18);background:var(--paper);overflow:hidden}
.frame.mailing-frame{left:12px}
.frame.sales-frame{left:605px}
.postcard{position:absolute;left:0;top:0;width:1120px;height:725px;background:var(--paper);overflow:hidden;transform:scale(.52);transform-origin:0 0}
.swoosh{position:absolute;inset:0}

/* Sales side */
.headline{position:absolute;right:60px;top:22px;text-align:right;color:#fff}
.headline .year{font-size:40px;font-weight:300;letter-spacing:1px}
.headline .year b{font-weight:900}
.headline .area{font-size:28px;font-weight:300;letter-spacing:1px}
.headline .area b{font-weight:900}
.sold-tag{position:absolute;right:80px;top:128px;background:var(--gold);color:#fff;font-weight:900;font-size:18px;padding:3px 20px;letter-spacing:1px}
.sales-table{position:absolute;left:470px;top:160px;width:625px;border-collapse:collapse;border:2px solid #9a9a9a;font-size:13px;color:var(--ink);background:#fff}
.sales-table th{background:var(--gold);color:#fff;font-weight:400;font-size:12.5px;padding:5px 4px;text-align:right}
.sales-table th:first-child,.sales-table td:first-child{text-align:left;padding-left:8px}
.sales-table td{padding:4px 4px;text-align:right;border-bottom:1px solid #e2e2e2}
.sales-table td:last-child,.sales-table th:last-child{padding-right:8px}
.footnote{position:absolute;left:470px;top:598px;font-size:12px;color:var(--ink)}
.agent{position:absolute;left:0;top:0;width:430px;height:725px}
.brand{position:absolute;left:70px;top:310px;display:flex;align-items:center;gap:10px;color:var(--ink);font-size:26px;font-weight:900;letter-spacing:1px}
.brand .mark{width:22px;height:22px;background:var(--gold)}
.portrait{position:absolute;border-radius:50%;border:4px solid #fff;box-shadow:0 0 0 2px var(--gray);background:radial-gradient(circle at 50% 40%,#c98a6e,#6e2a2a 60%,#2c4f5e)}
.agent .portrait{left:150px;top:370px;width:130px;height:130px}
.agent-name{position:absolute;left:0;width:430px;top:515px;text-align:center;color:var(--red);font-size:28px;font-weight:700;letter-spacing:1px}
.agent-role{position:absolute;left:0;width:430px;top:550px;text-align:center;color:var(--gold);font-size:17px;letter-spacing:1px}
.license{position:absolute;left:0;width:430px;top:578px;text-align:center;color:var(--muted);font-size:15px}
.contact{position:absolute;left:0;bottom:0;width:430px;height:108px;background:var(--red);color:#fff;text-align:center}
.contact .web{background:var(--red-dark);font-size:20px;font-weight:700;padding:5px 0}
.contact .phone{font-size:34px;font-weight:300;margin-top:4px}
.contact .email{font-size:17px}

/* Mailing side */
.pitch{position:absolute;left:50px;top:50px;color:#fff;line-height:1.1}
.pitch .lead{font-size:48px;font-weight:300}
.pitch .months{font-size:42px;font-weight:300}
.pitch .months b{font-weight:900}
.pitch .best{font-size:34px;font-weight:300}
.pitch .best b{font-weight:900}
.offers{position:absolute;left:50px;top:238px;background:#fff;color:var(--red);font-size:30px;font-weight:900;padding:6px 26px;border-radius:26px}
.prices{position:absolute;left:50px;top:300px;color:#fff;font-size:30px;font-weight:900}
.wait{position:absolute;left:50px;top:412px;color:var(--red);font-size:40px;font-weight:300}
.call-bar{position:absolute;left:0;top:470px;width:600px;background:var(--gold);color:#fff;font-size:24px;font-weight:700;padding:10px 0 10px 50px}
.body-copy{position:absolute;left:50px;top:540px;width:540px;font-size:16px;line-height:1.4;color:var(--ink)}
.body-copy p+p{margin-top:10px}
.reach{position:absolute;left:650px;top:330px;width:320px;text-align:center;color:var(--red);font-size:24px;line-height:1.2}
.mail-agent .portrait{left:700px;top:40px;width:120px;height:120px}
.mail-agent .info{position:absolute;left:840px;top:88px;color:var(--ink)}
.mail-agent .name{color:var(--red);font-size:22px;font-weight:900;letter-spacing:1px}
.mail-agent .lic{font-size:14px;color:var(--muted)}
.mail-agent .phone{color:var(--red);font-size:28px;font-weight:300;margin-top:4px}
.mail-agent .email{font-size:15px}
.mail-agent .web{display:inline-block;margin-top:6px;background:var(--gold);color:#fff;font-size:15px;font-weight:700;padding:3px 14px;border-radius:12px}
</style>
</head>
<body>

<div class="frame mailing-frame">
<div class="postcard mailing-side">
  <svg class="swoosh" width="1120" height="725" viewBox="0 0 1120 725" aria-hidden="true">
    <path d="M0,0 H1120 V60 C900,66 770,110 690,200 C600,310 430,395 0,400 Z" fill="#d8232f"/>
    <path d="M0,414 C430,410 610,325 700,215 C770,130 900,80 1120,72" fill="none" stroke="#c9a12a" stroke-width="10"/>
    <path d="M0,430 C440,426 625,340 715,230 C785,145 910,95 1120,88" fill="none" stroke="#bdbdbd" stroke-width="5"/>
  </svg>

  <div class="pitch">
    <div class="lead">Traditionally</div>
    <div class="months"><b>FEB</b> through <b>APRIL</b></div>
    <div class="best">are the <b>best months to sell</b></div>
  </div>
  <div class="offers">Most Offers</div>
  <div class="prices">Highest Prices</div>
  <div class="wait">Don't Wait!</div>
  <div class="call-bar">Call Now for a Free Market Analysis</div>
  <div class="body-copy">
    <p>Our market continues growing locally with very low inventory. As prices remain high, now is the time to sell or move to a home that fits your family.</p>
    <p>I am a Harbor Crest agent. I can connect you with buyers anywhere in the world and can co-ordinate your move as seamlessly as possible across the country.</p>
  </div>

  <div class="reach">Our Listings are advertised Locally and in 40 countries!!</div>

  <div class="mail-agent">
    <div class="portrait" role="img" aria-label="Portrait photo of the agent"></div>
    <div class="info">
      <div class="name">DANA WHITFIELD</div>
      <div class="lic">License #01482937</div>
      <div class="phone">555-014-2290</div>
      <div class="email">dwhitfield@hcrealty.com</div>
      <div class="web">www.dwhitfield.com</div>
    </div>
  </div>
</div>
</div>

<div class="frame sales-frame">
<div class="postcard sales-side">
  <svg class="swoosh" width="1120" height="725" viewBox="0 0 1120 725" aria-hidden="true">
    <path d="M560,0 H1120 V140 C880,148 630,170 500,250 C450,282 420,320 400,360 C420,260 480,120 560,0 Z" fill="#d8232f"/>
    <path d="M400,372 C440,290 560,185 1120,148" fill="none" stroke="#c9a12a" stroke-width="10"/>
    <path d="M398,392 C450,305 580,200 1120,163" fill="none" stroke="#bdbdbd" stroke-width="5"/>
  </svg>

  <div class="headline">
    <div class="year"><b>2015</b> SALES</div>
    <div class="area">IN YOUR <b>NEIGHBORHOOD</b></div>
  </div>
  <div class="sold-tag">SOLD</div>

  <table class="sales-table">
    <thead>
      <tr><th>Address</th><th>BR</th><th>BA</th><th>Sq Ft</th><th>Lot Size</th><th>List Price</th><th>Sale Price</th><th>$/Sq Ft</th><th>DOM</th></tr>
    </thead>
    <tbody>
      <tr><td>388 Elm PL*</td><td>3</td><td>3 1/2</td><td>2588</td><td>9239</td><td>3088000</td><td>3,100,000</td><td>1198</td><td>9</td></tr>
      <tr><td>3651 Birch ST</td><td>4</td><td>3</td><td>2228</td><td>6147</td><td>2998000</td><td>3000000</td><td>1346</td><td>23</td></tr>
      <tr><td>265 Brookview DR</td><td>4</td><td>3</td><td>2185</td><td>7040</td><td>2500000</td><td>2925000</td><td>1339</td><td>8</td></tr>
      <tr><td>431 Fawn AVE*</td><td>4</td><td>2</td><td>1611</td><td>13237</td><td>2498000</td><td>2610000</td><td>1620</td><td>8</td></tr>
      <tr><td>4127 Lake AVE*</td><td>3</td><td>2</td><td>2227</td><td>8700</td><td>2295000</td><td>2595000</td><td>1165</td><td>18</td></tr>
      <tr><td>72 Lindenwood CIR*</td><td>4</td><td>2</td><td>1364</td><td>5917</td><td>1788000</td><td>2525000</td><td>1851</td><td>16</td></tr>
      <tr><td>3669 Ravena CIR</td><td>4</td><td>2</td><td>1646</td><td>6404</td><td>2500000</td><td>2475000</td><td>1504</td><td>7</td></tr>
      <tr><td>414 Aspen PL*</td><td>3</td><td>2</td><td>1674</td><td>11200</td><td>2498000</td><td>2450000</td><td>1464</td><td>97</td></tr>
      <tr><td>295 Brookview DR*</td><td>3</td><td>2</td><td>1690</td><td>8178</td><td>2199000</td><td>2400000</td><td>1420</td><td>7</td></tr>
      <tr><td>307 Brookview DR.</td><td>3</td><td>2</td><td>1674</td><td>8538</td><td>2200000</td><td>2268000</td><td>1350</td><td>6</td></tr>
      <tr><td>97 Lindenwood CIR</td><td>4</td><td>2</td><td>1243</td><td>6080</td><td>1488000</td><td>2250000</td><td>1810</td><td>12</td></tr>
      <tr><td>3706 Corwin CIR*</td><td>3</td><td>2</td><td>1333</td><td>6493</td><td>1895500</td><td>2227500</td><td>1671</td><td>17</td></tr>
      <tr><td>376 Hillcrest DR*</td><td>3</td><td>2</td><td>1740</td><td>6324</td><td>2200000</td><td>2180000</td><td>1253</td><td>11</td></tr>
      <tr><td>3643 Birch ST</td><td>4</td><td>2</td><td>1474</td><td>6111</td><td>1799000</td><td>2115000</td><td>1435</td><td>20</td></tr>
      <tr><td>64 Lindenwood Cir</td><td>4</td><td>2</td><td>1456</td><td>6111</td><td>1788000</td><td>2000000</td><td>1374</td><td>11</td></tr>
      <tr><td>258 Fairmont CT</td><td>3</td><td>2</td><td>1428</td><td>10,624</td><td>1,950,000</td><td>2,100,000</td><td>1471</td><td>20</td></tr>
    </tbody>
  </table>
  <p class="footnote">* indicates Harbor Crest Realtors listing or sale. This information is deemed reliable, but not verified or guaranteed.</p>

  <div class="agent">
    <div class="brand"><span class="mark"></span>HARBOR CREST</div>
    <div class="portrait" role="img" aria-label="Portrait photo of the agent"></div>
    <div class="agent-name">DANA WHITFIELD</div>
    <div class="agent-role">RELOCATION SPECIALIST</div>
    <div class="license">California License #01482937</div>
    <div class="contact">
      <div class="web">www.dwhitfield.com</div>
      <div class="phone">555-014-2290</div>
      <div class="email">dwhitfield@hcrealty.com</div>
    </div>
  </div>
</div>
</div>

</body>
</html>
```